New business card, letter head, email signature and Portfolio for our Security company.

We are an Crest security company that provides a top quality manpower services to protect high rise buildings, retail and all type of properties and would like a new business card/logo look.

- We would like the spot UV design.
- Matt black (double sided).
- We would like to incorporate a royal blue colour (feel free to experiment with it).
- Feel free to try different lengths with the card to make it stand out more than a normal business card.
- We would like the logo to be an eagle eye in the background (shines when card is tilted slightly in the background, either on the front, back or both sides of the card). Image attached as an example of eye shape (colour to be either black or royal blue).
- HARBOUR CREST SECURITY SERVICES PTY. LTD. and HCSS to be placed on one side of the card and on the other side of the card to have;

- Name in slightly bigger font than the position (directly on the bottom on the name).
- Mobile number
- Email address
- Website email address
- PO BOX address

Can we please have the files in a format that we can edit.

Reason: I need to consult my business partner with the designs so far and will make a decision from there.

Target Market(s)

Security Industry

Industry/Entity Type

Business

Contact Information for Business Card

- Mobile number
- Email address
- Website email address
- PO BOX address

Logo Text

HCSS and underneath the HCSS please add HARBOUR CREST SECURITY SERVICES PTY. LTD.

Font styles to use
Other font styles liked:
• bold type font

Colors
0255a3
000000

Requirements
Must have
• We are an Crest security company that provides a top quality manpower services to protect high rise buildings, retail and all type of properties and would like a new business card/logo look.
• - We would like the spot UV design.
• - Matt black (double sided).
• - We would like to incorporate a royal blue colour (feel free to experiment with it).
• - Feel free to try different lengths with the card to make it stand out more than a normal business card.
• - We would like the logo to be an eagle eye in the background (shines when card is tilted slightly in the background, either on the front, back or both sides of the card). Image attached as an example of eye shape (colour to be either black or royal blue).
• - HARBOUR CREST SECURITY SERVICES PTY. LTD. and HCSS to be placed on one side of the card and on the other side of the card to have;
• - Name in slightly bigger font than the position (directly on the bottom on the name).
• - Mobile number
• - Email address
• - Website email address
• - PO BOX address
• Can we please have the files in a format that we can edit.
Nice to have
• Feel free to try different lengths with the card to make it stand out more than a normal business card.
• Please find "URBAN JUNGLE" font attached and incorporate HCSS into the same style with building's inside the HCSS bold front also add HARBOUR into the bottom part of the S and follow on E - Crest on the bottom S - SECURITY on the bottom S - SERVICES on the bottom of each letter.
• other than that, I'll be happy with a bold modern font for the HCSS and HARBOUR CREST SECURITY SERVICES in a bold and thinner font underneath.

```html
<!DOCTYPE html>
<html lang="en">
<head>
<meta charset="utf-8">
<title>Harbour Crest Security – Business Card</title>
<link rel="stylesheet" href="https://fonts.googleapis.com/css2?family=Exo+2:wght@700;800&family=Open+Sans:wght@400;600&display=swap">
<style>
  :root {
    --backdrop: #1e1e1f;
    --card: #ffffff;
    --ink: #111111;
    --royal: #2a3a8f;
    --grey: #8a8a8a;
    --body: #333333;
    --rule: #222222;
  }
  * { box-sizing: border-box; margin: 0; padding: 0; }
  html, body { width: 1200px; height: 1000px; overflow: hidden; }
  body {
    background: var(--backdrop);
    font-family: "Open Sans", Arial, sans-serif;
    position: relative;
  }
  .card {
    position: absolute;
    left: 190px;
    width: 820px;
    height: 460px;
    background: var(--card);
    border-radius: 40px;
  }
  .card--front { top: 30px; }
  .card--back { top: 510px; }

  .brand {
    position: absolute;
    display: flex;
    align-items: center;
    gap: 14px;
  }
  .brand__dot {
    width: 34px; height: 34px;
    border-radius: 50%;
    background: var(--royal);
    flex: none;
  }
  .brand__name {
    font-family: "Exo 2", Arial, sans-serif;
    font-weight: 800;
    color: var(--ink);
    letter-spacing: 0.5px;
    white-space: nowrap;
  }
  .card--front .brand { left: 50%; top: 170px; transform: translateX(-50%); }
  .card--front .brand__name { font-size: 40px; }

  .front__web {
    position: absolute;
    left: 0; right: 0; bottom: 70px;
    text-align: center;
    color: var(--royal);
    font-size: 18px;
    letter-spacing: 3px;
  }

  .card--back .brand { left: 70px; top: 80px; gap: 10px; }
  .card--back .brand__dot { width: 24px; height: 24px; }
  .card--back .brand__name { font-size: 26px; }

  .back__rule {
    position: absolute;
    left: 470px; right: 50px; top: 94px;
    height: 1px; background: var(--rule);
  }
  .back__address {
    position: absolute;
    right: 55px; top: 150px;
    text-align: right;
    font-size: 17px;
    line-height: 1.35;
    color: var(--body);
  }
  .person {
    position: absolute;
    left: 80px; top: 262px;
  }
  .person__name {
    font-family: "Exo 2", Arial, sans-serif;
    font-weight: 800;
    font-size: 34px;
    line-height: 1;
    color: var(--royal);
  }
  .person__surname { color: var(--grey); }
  .person__role {
    margin-top: 6px;
    font-size: 18px;
    color: var(--body);
    padding-bottom: 8px;
    border-bottom: 1px solid var(--rule);
    width: 250px;
  }
  .contacts {
    list-style: none;
    margin-top: 12px;
  }
  .contacts__item {
    display: flex;
    align-items: center;
    gap: 12px;
    font-size: 17px;
    line-height: 27px;
    color: var(--body);
  }
  .contacts__icon { width: 14px; height: 14px; flex: none; fill: var(--royal); }
  .contacts__accent { color: var(--royal); }
</style>
</head>
<body>
  <section class="card card--front">
    <div class="brand">
      <span class="brand__dot"></span>
      <span class="brand__name">HARBOUR CREST SECURITY</span>
    </div>
    <p class="front__web">www.websitename.com</p>
  </section>

  <section class="card card--back">
    <div class="brand">
      <span class="brand__dot"></span>
      <span class="brand__name">HARBOUR CREST SECURITY</span>
    </div>
    <div class="back__rule"></div>
    <p class="back__address">Your Street Address,<br>Harbourview City, 1234</p>

    <div class="person">
      <p class="person__name">DANIEL <span class="person__surname">REEVES</span></p>
      <p class="person__role">OWNER</p>
      <ul class="contacts">
        <li class="contacts__item">
          <svg class="contacts__icon" viewBox="0 0 24 24"><path d="M6.6 10.8a15.1 15.1 0 0 0 6.6 6.6l2.2-2.2c.3-.3.7-.4 1-.2 1.1.4 2.3.6 3.6.6.6 0 1 .4 1 1V20c0 .6-.4 1-1 1A17 17 0 0 1 3 4c0-.6.4-1 1-1h3.5c.6 0 1 .4 1 1 0 1.3.2 2.5.6 3.6.1.3 0 .7-.2 1z"/></svg>
          +000 987 654 321
        </li>
        <li class="contacts__item">
          <svg class="contacts__icon" viewBox="0 0 24 24"><path d="M2 5h20v14H2z" fill="none"/><path d="M2 5h20v2l-10 6L2 7zM2 9l10 6 10-6v10H2z"/></svg>
          yourname@email.com
        </li>
        <li class="contacts__item">
          <svg class="contacts__icon" viewBox="0 0 24 24"><path d="M10 2a8 8 0 0 1 6.3 12.9l5.4 5.4-1.4 1.4-5.4-5.4A8 8 0 1 1 10 2zm0 3a5 5 0 1 0 0 10 5 5 0 0 0 0-10z"/></svg>
          <span>www.<span class="contacts__accent">websitename</span>.com</span>
        </li>
      </ul>
    </div>
  </section>
</body>
</html>
```